Web Design / Transformation our Joomla web site

Job Type
We are looking for a fresh eye-catching Custom Joomla Design to transform our Joomla web site

Task Description
We are in a process to create web site to Speech Pathology services . The site is built by using brightpanel ((http://www.brightpanel-demo.com/) meadow template.

You can see our site http://beyondtalkclinic-demo.com/demo

Unfortunately, this template does not match our identity. We would like to improve or replace it. Although we like features that brightpanel template is giving as part of their template ,we want to transform our site to something more simplistic and kids oriented . We don’t like look and fill of our website since it’s very professional and “corporate” . Our business is very small and is not 100 people company , we are looking for something more simple and personal. It should look professional, all be it, child friendly. We work on children’s communication skills, and we want to convey an idea that communication is “Beyond The Talk”, meaning children need to learn to play and socialize appropriately. In addition, learning to be a better communicators will help them to be closer to their family members and friends. We want our website to show kids playing and having fun. In other hand , we don't want the Website to be too busy with images, so use your professional judgment.
You can change current template or you can provide your own Joomla design.

Examples of website look that we like :

http://parentvoicehelp-demo.com
http://thevocalfriends-demo.blogspot.com/
http://brindleclinicvoice-demo.com/

About Our Company :
Company name: Beyond The Talk
What we do: Pediatric Speech & Language Pathology Services. We established Beyond The Talk to provide families with a unique option for their child’s speech therapy needs. Our clinic is founded on the principle that all children are different and require a thoughtful, parent-driven therapy plan. When a family chooses us, they will enter a partnership with an experienced, well-trained therapist.
Top Three Things to Communicate through our Website:
#1 - We are kids friendly
#2 - We are professional
#3 - We provide our services with a loving, nurturing attitude toward the child and with compassionate, comprehensive support and input for the family
Updates

To see current running site : http://beyondtalkclinic-demo.com/demo/

Reason: There are no good designs to address our needs

Reason: It's still work in progress. Submitted designs are still under constructions and waiting for updates

We are accepting WordPress designs as well !!!

Target Market(s)

Families with kids

Industry/Entity Type

Communication

Requirements
Must have
• • Joomla/Wordpress as a platform
• Easy to Navigate
• Clean Design, kids friendly but professional

```html
<!DOCTYPE html>
<html lang="en">
<head>
<meta charset="utf-8">
<title>Beyond The Talk – About Us</title>
<link href="https://fonts.googleapis.com/css2?family=Roboto:wght@400;500&family=Roboto+Condensed:wght@400&family=Arimo:wght@400&display=swap" rel="stylesheet">
<style>
:root{
  --top-bar:#0d5a86;
  --sky-top:#bcd6ec;
  --sky-mid:#dfeaf4;
  --sky-low:#f3f6f9;
  --heading:#666a6e;
  --nav:#555a5e;
  --nav-active:#6b9a2a;
  --body-text:#666666;
  --rule:#dcdfe2;
  --panel-border:#d6d8da;
  --link:#1ea2d8;
  --button:#08aeea;
  --meadow-top:#b8d84e;
  --meadow-low:#93c23e;
  --white:#ffffff;
}
*{box-sizing:border-box;margin:0;padding:0}
html,body{width:1200px;height:1000px;overflow:hidden}
body{font-family:"Arimo",Arial,sans-serif;color:var(--body-text);background:var(--sky-low)}
h1,h2{font-weight:400}
.canvas{position:relative;width:1200px;height:1000px;overflow:hidden;
  background:linear-gradient(180deg,var(--sky-top) 0%,var(--sky-mid) 25%,var(--sky-low) 55%,var(--white) 80%)}
.top-bar{position:absolute;left:0;top:0;width:1200px;height:6px;background:var(--top-bar)}

.brand{position:absolute;left:122px;top:62px;display:flex;align-items:center;gap:8px}
.brand-dot{width:22px;height:22px;border-radius:50%;background:var(--link)}
.brand-name{font-family:"Roboto",sans-serif;font-weight:500;font-size:22px;color:var(--link)}
.brand-tag{position:absolute;left:127px;top:132px;font-family:"Roboto",sans-serif;font-size:8px;color:var(--top-bar)}

.search{position:absolute;left:783px;top:31px;width:292px;height:41px;background:var(--white);border:1px solid #cfd3d6;box-shadow:0 1px 2px rgba(0,0,0,.08)}
.search-btn{position:absolute;right:0;top:0;width:40px;height:39px;border-left:1px solid #e0e0e0}

.main-nav{position:absolute;right:105px;top:110px;display:flex;font-family:"Roboto",sans-serif;font-weight:500;font-size:14px;letter-spacing:.2px}
.main-nav a{color:var(--nav);text-decoration:none;padding:4px 19px;line-height:18px;border-left:1px solid #c9d1d8}
.main-nav a:first-child{border-left:none}
.main-nav a.active{color:var(--nav-active)}
.header-rule{position:absolute;left:120px;top:169px;width:960px;border-top:1px solid #c3c9cf;border-bottom:1px solid #eef0f2;height:3px}

.content{position:absolute;left:119px;top:206px;width:630px}
.page-title{font-family:"Roboto Condensed",sans-serif;font-size:26px;color:var(--heading);padding-bottom:9px;border-bottom:1px solid var(--rule)}
.feature-photo{margin-top:15px;width:630px;height:240px;background:linear-gradient(90deg,#c98d63 0%,#2f8d59 30%,#e8ddd0 55%,#d6a680 80%,#c5885a 100%)}
.content p{font-size:12.1px;line-height:18px;text-align:justify;margin-top:5px}
.content p+p{margin-top:18px}
.content-rule{border-top:1px solid var(--rule);margin-top:5px}

.panel{position:absolute;left:778px;width:302px;background:var(--white);border:1px solid var(--panel-border)}
.newsletter{top:213px;height:140px;padding:12px 9px}
.panel-title{font-family:"Roboto Condensed",sans-serif;font-size:19px;color:#222}
.email-field{margin-top:10px;height:38px;border:1px solid #cfd3d6;border-radius:3px;font-size:12px;color:#888;padding:11px 6px}
.subscribe{position:absolute;right:10px;top:95px;background:var(--button);color:var(--white);font-family:"Roboto Condensed",sans-serif;font-size:17px;padding:8px 10px;border-radius:2px}
.popular{top:368px;height:293px}
.popular .panel-title{color:var(--heading);padding:10px 6px 8px;border-bottom:1px solid var(--rule)}
.post{padding:8px 5px 12px;border-bottom:1px solid var(--rule)}
.post:last-child{border-bottom:none}
.post-link{font-size:12.2px;color:var(--link);display:block;margin-bottom:6px}
.post-text{font-size:12.2px;line-height:14.5px;text-align:justify;color:#555}
.social{top:676px;height:51px;display:flex;justify-content:center;align-items:center;gap:14px}
.social span{width:29px;height:29px;border-radius:3px}

.partners{position:absolute;left:120px;top:785px;width:961px;height:75px}
.partner{position:absolute;border-radius:4px}

.meadow{position:absolute;left:0;top:880px;width:1200px;height:120px;
  background:linear-gradient(180deg,var(--meadow-top) 0%,var(--meadow-low) 100%)}
</style>
</head>
<body>
<div class="canvas">
  <div class="top-bar"></div>

  <div class="brand"><span class="brand-dot"></span><span class="brand-name">Beyond The Talk</span></div>
  <div class="brand-tag">Speech &amp; Language Pathology Services</div>

  <div class="search">
    <div class="search-btn">
      <svg width="40" height="39" viewBox="0 0 40 39"><circle cx="18" cy="17" r="5" fill="none" stroke="#222" stroke-width="2.5"/><line x1="22" y1="20" x2="28" y2="25" stroke="#222" stroke-width="3"/></svg>
    </div>
  </div>

  <nav class="main-nav">
    <a href="#">HOME</a><a href="#" class="active">ABOUT</a><a href="#">TREATMENT TECHNIQUES</a><a href="#">BLOG</a><a href="#">FAQ</a><a href="#">RESOURCES</a>
  </nav>
  <div class="header-rule"></div>

  <main class="content">
    <h1 class="page-title">ABOUT US</h1>
    <div class="feature-photo" role="img" aria-label="Therapist talking with a young girl in a bright playroom"></div>
    <p>Sed ut perspiciatis unde omnis iste natus error sit voluptatem accusantium doloremque laudantium, totam rem aperiam, eaque ipsa quae ab illo inventore veritatis et quasi architecto beatae vitae dicta sunt explicabo.</p>
    <p>Nemo enim ipsam voluptatem quia voluptas sit aspernatur aut odit aut fugit, sed quia consequuntur magni dolores eos qui ratione voluptatem sequi nesciunt. Neque porro quisquam est, qui dolorem ipsum quia dolor sit amet, consectetur, adipisci velit, sed quia non numquam eius modi tempora incidunt ut labore et dolore magnam aliquam quaerat voluptatem.</p>
    <p>Ut enim ad minima veniamNemo enim ipsam voluptatem quia voluptas sit aspernatur aut odit aut fugit, sed quia consequuntur magni dolores eos qui ratione voluptatem sequi nesciunt. Neque porro quisquam est, qui dolorem ipsum quia dolor sit amet, consectetur, adipisci velit, sed quia non numquam eius modi tempora incidunt ut labore et dolore magnam aliquam quaerat voluptatem. Ut enim ad minima veniam</p>
    <div class="content-rule"></div>
  </main>

  <aside>
    <div class="panel newsletter">
      <h2 class="panel-title">NEWSLETTER SIGN UP</h2>
      <div class="email-field">Enter Your Email</div>
      <div class="subscribe">SUBSCRIBE</div>
    </div>
    <div class="panel popular">
      <h2 class="panel-title">POPULAR POSTS</h2>
      <div class="post"><a class="post-link">Lorem ipsum dolor sit amet</a><p class="post-text">Lorem ipsum dolor sit amet, consectetur adipisicing elit, sed do eiusmod tempor incididunt ut labore et dolore magna aliqua.</p></div>
      <div class="post"><a class="post-link">Lorem ipsum dolor sit amet</a><p class="post-text">Lorem ipsum dolor sit amet, consectetur adipisicing elit, sed do eiusmod tempor incididunt ut labore et dolore magna aliqua.</p></div>
      <div class="post"><a class="post-link">Lorem ipsum dolor sit amet</a><p class="post-text">Lorem ipsum dolor sit amet, consectetur adipisicing elit, sed do eiusmod tempor incididunt ut labore et dolore magna aliqua.</p></div>
    </div>
    <div class="panel social">
      <span style="background:#3b5998"></span><span style="background:#6cc5ea"></span><span style="background:#1a78b4"></span><span style="background:#f08a24"></span><span style="background:#7fb141"></span>
    </div>
  </aside>

  <div class="partners">
    <div class="partner" style="left:2px;top:10px;width:128px;height:62px;background:#e4e4e4"></div>
    <div class="partner" style="left:166px;top:14px;width:172px;height:60px;background:#d9dcea"></div>
    <div class="partner" style="left:380px;top:24px;width:150px;height:36px;background:#e2e2e2"></div>
    <div class="partner" style="left:568px;top:0;width:160px;height:58px;background:#d3e1ef"></div>
    <div class="partner" style="left:756px;top:0;width:205px;height:57px;background:#4b7fb6;border-radius:0"></div>
  </div>

  <div class="meadow" role="img" aria-label="Green rolling hills with small trees along the page footer"></div>
</div>
</body>
</html>
```